Real Estate Company Looking for Business Card Designs for 3 Executives

Hello!
Thanks so much for considering our project! We are a real estate investment company located in Edmonton, Alberta called Bellhaven Group of Companies. We invest/develop both commercial and residential real estate and are looking to create 3 DOUBLE-SIDED business cards for 3 top executives in the company! (for some reason it won't let us select the double-sided option, but yes, the cards are double sided and would be happy to tip extra)

We have certain guidelines that we want our business cards to for sure follow - the back of the Business card has to be the Black Background Version of the Logo which has already been designed and linked as a file (first file). We want the entire back of the card to simply just be the black background logo. In terms of the front of the card, would like to see a smaller version of the white background logo (linked as the second file) in the top left hand corner - of course, feel free to get creative and we can make revisions together along the way! and Then after that, just text. We want the card to be sharp, clean, easy on the eyes and highly professional looking. We would like the card to include the Full name of the Company (Bellhaven Group of Companies), Name of the Person, Title, Phone, Email. If possible please provide the front part of the card for 3 people:

1) Bellhaven Group of Companies, Liora Quenby, Chief Financial Officer, 780-555-0142, lioraquenby@bellhavengroup.example

2) Bellhaven Group of Companies, Tobias Quenby, Chief Executive Officer, 780-555-0187, tobiasquenby@bellhavengroup.example

3) Bellhaven Group of Companies, Rui Delcourt, Chief Operations Officer, 587-555-0163, ruidelcourt@bellhavengroup.example

Thank you so much for considering our project & we look forward to seeing your designs!

```html
<!DOCTYPE html>
<html lang="en">
<head>
<meta charset="utf-8">
<title>Bellhaven Group of Companies – Business Card</title>
<link rel="stylesheet" href="https://fonts.googleapis.com/css2?family=Jost:wght@400&family=Tinos:wght@700&family=Arimo:wght@400&display=swap">
<style>
  :root {
    --backdrop: #2a2a2a;
    --card: #1f1f1f;
    --ink: #ffffff;
    --ink-soft: #e8e8e8;
    --emboss: #2e2e2e;
  }
  * { margin: 0; padding: 0; box-sizing: border-box; }
  html, body {
    width: 1200px;
    height: 1059px;
    overflow: hidden;
    background: var(--backdrop);
  }
  .canvas { position: relative; width: 1200px; height: 1059px; }
  .card {
    position: absolute;
    width: 688px;
    height: 392px;
    background: var(--card);
    border-radius: 18px;
  }
  .card--front { left: 257px; top: 89px; }
  .card--back { left: 255px; top: 547px; }

  .brand {
    position: absolute;
    left: 0; right: 0; top: 70px;
    text-align: center;
    color: var(--ink);
    font-family: "Jost", sans-serif;
    font-weight: 400;
  }
  .brand__name {
    font-size: 50px;
    letter-spacing: 12px;
    padding-left: 12px;
    line-height: 1;
  }
  .brand__tagline {
    display: flex;
    align-items: center;
    justify-content: center;
    gap: 8px;
    margin-top: 38px;
    font-size: 10px;
    letter-spacing: 3px;
  }
  .brand__rule { width: 32px; height: 1px; background: var(--ink); }

  .person {
    position: absolute;
    right: 394px;
    top: 270px;
    text-align: right;
    color: var(--ink);
  }
  .person__name {
    font-family: "Tinos", serif;
    font-weight: 700;
    font-size: 23px;
    letter-spacing: 0.5px;
    line-height: 1.2;
    margin-top: 8px;
  }
  .person__title {
    font-family: "Arimo", sans-serif;
    font-size: 15.5px;
    margin-top: 2px;
  }
  .divider {
    position: absolute;
    left: 311px; top: 270px;
    width: 1px; height: 65px;
    background: var(--ink-soft);
  }
  .contacts {
    position: absolute;
    left: 334px; top: 264px;
    list-style: none;
    font-family: "Arimo", sans-serif;
    font-size: 16.5px;
    color: var(--ink);
  }
  .contacts li {
    display: flex;
    align-items: center;
    gap: 7px;
    height: 26px;
  }
  .contacts svg { width: 13px; height: 13px; fill: var(--ink); flex: none; }

  .back-mark {
    position: absolute;
    left: 0; right: 0; top: 150px;
    text-align: center;
    font-family: "Jost", sans-serif;
    font-weight: 400;
    font-size: 76px;
    letter-spacing: 10px;
    padding-left: 10px;
    line-height: 1;
    color: var(--emboss);
  }
</style>
</head>
<body>
<main class="canvas">
  <section class="card card--front" aria-label="Card front">
    <div class="brand">
      <div class="brand__name">BELLHAVEN</div>
      <div class="brand__tagline">
        <span class="brand__rule"></span>
        <span>GROUP OF COMPANIES</span>
        <span class="brand__rule"></span>
      </div>
    </div>

    <div class="person">
      <div class="person__name">TOBIAS QUENBY</div>
      <div class="person__title">Chief Executive Officer</div>
    </div>
    <span class="divider"></span>
    <ul class="contacts">
      <li>
        <svg viewBox="0 0 24 24" aria-hidden="true"><path d="M6.6 10.8a15.1 15.1 0 0 0 6.6 6.6l2.2-2.2a1 1 0 0 1 1-.25 11.4 11.4 0 0 0 3.6.57 1 1 0 0 1 1 1V20a1 1 0 0 1-1 1A17 17 0 0 1 3 4a1 1 0 0 1 1-1h3.5a1 1 0 0 1 1 1c0 1.25.2 2.45.57 3.6a1 1 0 0 1-.25 1z"/></svg>
        <span>780-555-0187</span>
      </li>
      <li>
        <svg viewBox="0 0 24 24" aria-hidden="true"><path d="M2 5h20v14H2zm2 2v.4l8 5.3 8-5.3V7zm0 2.8V17h16V9.8l-8 5.3z"/></svg>
        <span>tobiasquenby@bellhavengroup.example</span>
      </li>
      <li>
        <svg viewBox="0 0 24 24" aria-hidden="true"><path d="M12 2a10 10 0 1 0 0 20 10 10 0 0 0 0-20zm-1 17.9A8 8 0 0 1 4.2 10L9 14.8v1a2 2 0 0 0 2 2zm6.9-2.5A2 2 0 0 0 16 16h-1v-3a1 1 0 0 0-1-1H8v-2h2a1 1 0 0 0 1-1V7h2a2 2 0 0 0 2-2v-.4a8 8 0 0 1 2.9 12.8z"/></svg>
        <span>www.bellhavengroup.example</span>
      </li>
    </ul>
  </section>

  <section class="card card--back" aria-label="Card back">
    <div class="back-mark">BELLHAVEN</div>
  </section>
</main>
</body>
</html>
```